Design website for new email startup

We are starting a company called Pingo.QZ (it will live at http://pingo.qz).

We would like the main landing page for our site designed. We have provided a very simple wireframe to help provide direction for the content it should include, but we do not expect the designers to adhere to it at all - we encourage unique ideas. There is some sample text in the wireframe - this does not have to be used, but may provide ideas.

We provide an easy way for people to manage email for a custom domain name. For example if you own "yourhouseword.example" you can point your DNS records to us and we'll make it easy to have emails addressed to your domain get forwarded to your existing email (gmail, etc). Folks running blogs, and other small sites can quickly setup email addresses for their domains and manage them in one place.

(For technical folks, we have you point your dns mx records to us, hence the name. That way all your email hits us and we can redirect it wherever you want. We make it easy to manage a single domain or a bunch of domains. Many domain registrars offer this service for a fee, and have clumsy management tools. We provide a robust simple toolset for free, as well as premium options).

The goal of the landing page is to get folks into the signup flow. The second priority flow is to have them take a look at the premium plan offerings.

We may offer the winning designer additional work for the remainder of the site design.
Updates

I've changed this project to a committed payment.  It is no longer refundable.  Thank you.

Target Market(s)

Bloggers, podcasters, designers, app developers - people who are a little tech savvy.

Industry/Entity Type

It Company

Font styles to use
Sans Serif

Colors

Designer to choose colors to be used in the design.

Requirements
Must have
• A full fidelity mockup (comp) of the landing page including the source file (psd, ai, etc).

Some sort of logo treatment for the pingo.qz brand

A call to action for signup, such as the suggested 'Get Started Here'
Nice to have
• A hip startup feel

Incorporation of the email theme

Give the impression it is simple, easy and fast

```html
<!DOCTYPE html>
<html lang="en">
<head>
<meta charset="utf-8">
<title>Pingo.QZ — We make email easy</title>
<link rel="stylesheet" href="https://fonts.googleapis.com/css2?family=Open+Sans:wght@400;600;700&display=swap">
<style>
  :root {
    --orange: #e8650f;
    --orange-light: #f28a22;
    --orange-dark: #d9580a;
    --ink: #1c1c1c;
    --text: #3a3a3a;
    --cream: #efe9dd;
    --white: #ffffff;
    --footer-top: #262626;
    --footer-bottom: #0e0e0e;
    --footer-heading: #dcd6c8;
    --muted: #8a8a8a;
    --dot: #c9c9c9;
    --divider: #444444;
    --social: #2f8fd1;
  }
  * { box-sizing: border-box; margin: 0; padding: 0; }
  html, body { width: 1200px; height: 1134px; overflow: hidden; }
  body { font-family: "Open Sans", Arial, sans-serif; background: var(--white); position: relative; }

  .site-header { position: absolute; left: 0; top: 0; width: 1200px; height: 129px; background: var(--white); }
  .brand { position: absolute; left: 66px; top: 38px; font-size: 44px; font-weight: 700; color: var(--ink); letter-spacing: 0.5px; }
  .main-nav { position: absolute; right: 67px; top: 52px; display: flex; align-items: center; gap: 7px; font-size: 15px; color: var(--orange); }
  .main-nav svg { margin-left: 10px; }

  .hero { position: absolute; left: 0; top: 129px; width: 1200px; height: 491px;
    background: linear-gradient(135deg, #2a3550 0%, #7d6f5e 35%, #b9a68b 55%, #3b4a68 80%, #1d2740 100%); }
  .hero-title { position: absolute; left: 67px; top: 214px; font-size: 30px; font-weight: 600; color: var(--white); }
  .hero-actions { position: absolute; left: 69px; top: 285px; display: flex; gap: 8px; }
  .btn { height: 57px; display: flex; align-items: center; justify-content: center;
    background: linear-gradient(var(--orange-light), var(--orange-dark)); color: var(--white);
    font-size: 19px; font-weight: 600; }
  .btn-primary { width: 184px; }
  .btn-secondary { width: 172px; }
  .slider-dots { position: absolute; left: 557px; top: 433px; display: flex; gap: 9px; }
  .slider-dots span { width: 15px; height: 15px; border-radius: 50%; background: var(--dot); }
  .slider-dots span.active { background: var(--orange); }

  .features { position: absolute; left: 0; top: 620px; width: 1200px; height: 350px; background: var(--cream); }
  .feature-card { position: absolute; top: 44px; width: 520px; height: 261px; background: var(--white); border-radius: 4px; }
  .feature-card.first { left: 67px; }
  .feature-card.second { left: 612px; }
  .feature-art { position: absolute; left: 20px; top: 51px; width: 126px; height: 147px; border-radius: 8px; }
  .art-mail { background: radial-gradient(circle, #e9eef6 30%, #4a9be0 75%, #1f6fc4 100%); }
  .art-mascot { background: radial-gradient(circle, #fff 35%, #c7d84a 65%, #f08a24 100%); }
  .feature-title { position: absolute; left: 176px; top: 46px; width: 320px; font-size: 17px; font-weight: 400; color: var(--text); line-height: 21px; }
  .feature-text { position: absolute; left: 176px; top: 98px; width: 318px; font-size: 14.5px; line-height: 18px; color: var(--text); text-align: justify; hyphens: auto; }
  .feature-card.second .feature-title { left: 176px; }
  .feature-card.second .feature-text { left: 180px; }

  .site-footer { position: absolute; left: 0; top: 970px; width: 1200px; height: 164px;
    border-top: 4px solid var(--orange); background: linear-gradient(var(--footer-top), var(--footer-bottom)); }
  .contact-title { position: absolute; left: 68px; top: 14px; font-size: 25px; font-weight: 400; color: var(--footer-heading); }
  .contact-brand { position: absolute; left: 68px; top: 64px; font-size: 18px; font-weight: 600; color: var(--orange-light); }
  .contact-details { position: absolute; left: 68px; top: 86px; display: flex; gap: 32px; font-size: 15px; font-weight: 600; color: var(--white); }
  .footer-divider { position: absolute; left: 461px; top: 13px; width: 1px; height: 111px; background: var(--divider); }
  .social-links { position: absolute; right: 67px; top: 52px; display: flex; gap: 10px; font-size: 14px; font-weight: 600; color: var(--white); }
  .social-links span { display: flex; align-items: center; gap: 5px; }
  .social-links i { width: 10px; height: 10px; background: var(--social); display: inline-block; }
  .copyright { position: absolute; right: 67px; top: 108px; font-size: 14.5px; color: var(--muted); }
</style>
</head>
<body>
  <header class="site-header">
    <div class="brand">PINGO.QZ</div>
    <nav class="main-nav">
      <span>HOW IT WORKS</span><span>|</span>
      <span>SUPPORT</span><span>|</span>
      <span>LOGIN</span>
      <svg width="24" height="24" viewBox="0 0 24 24" aria-hidden="true">
        <circle cx="12" cy="12" r="11" fill="#6b6b6b"/>
        <rect x="7.5" y="11" width="9" height="7" rx="1" fill="#fff"/>
        <path d="M9.5 11 V8.5 a2.5 2.5 0 0 1 5 0 V11" fill="none" stroke="#fff" stroke-width="1.6"/>
      </svg>
    </nav>
  </header>

  <section class="hero" role="img" aria-label="Photo of a team working at a round table with a laptop showing a chart">
    <h1 class="hero-title">WE MAKE EMAIL EASY</h1>
    <div class="hero-actions">
      <a class="btn btn-primary">GET STARTED FREE</a>
      <a class="btn btn-secondary">COMPARE PRICE</a>
    </div>
    <div class="slider-dots"><span class="active"></span><span></span><span></span><span></span></div>
  </section>

  <section class="features">
    <article class="feature-card first">
      <div class="feature-art art-mail" role="img" aria-label="Illustration of an email envelope with an at sign and blue arrow"></div>
      <h2 class="feature-title">How to configure your Nimbleflare DNS to use pingo.qz</h2>
      <p class="feature-text">Your servers should make something useful, not just serve a bunch of static files. Your servers will be faster as soon as you save them from this kind of useless job.your servers should make something useful.</p>
    </article>
    <article class="feature-card second">
      <div class="feature-art art-mascot" role="img" aria-label="Illustration of a domain registrar mascot"></div>
      <h2 class="feature-title">Use pingo.qz with your Domainly</h2>
      <p class="feature-text">Your servers should make something useful, not just serve a bunch of static files. Your servers will be faster as soon as you save them from this kind of useless job.your servers should make something useful.</p>
    </article>
  </section>

  <footer class="site-footer">
    <h3 class="contact-title">Contact us</h3>
    <div class="contact-brand">PINGO.QZ</div>
    <div class="contact-details">
      <span>contact@pingo.qz.example</span>
      <span>Phone: +31.5550100200</span>
    </div>
    <div class="footer-divider"></div>
    <div class="social-links">
      <span><i></i>Linkly</span>
      <span><i></i>Facepage</span>
      <span><i></i>Chirper</span>
    </div>
    <div class="copyright">Copyright © 2014 pingo.qz, All Rights Reserved</div>
  </footer>
</body>
</html>
```